FinTech company looking to revamp and expand client-facing interface for our financial models

Pellworth Engines currently has a very simple website that allows clients to interact with our financial models. We are looking to completely redesign the current site and add several extra pages to provide extra functionality. We want the design to have a modern, slick feel, that will work on both a desktop or a tablet. It should be straightforward for clients to move between different pages at any time, and clear from the layout how to interact with the more advanced features. We have included screenshots of existing pages in the attached design brief, as well as sketches of the functionality required by the new pages, but can't provide a direct link to the current site.
Target Market(s)
Professional investors that will be paying to access the interface
Industry/Entity Type
Finance
Number of Pages Required
4 page
Colors
Designer to choose colors to be used in the design.
Look and feel
Each slider illustrates characteristics of the customer's brand and the style your logo design should communicate.

```html
<!DOCTYPE html>
<html lang="en">
<head>
<meta charset="utf-8">
<title>Pellworth Engines – Factor Models</title>
<link rel="stylesheet" href="https://fonts.googleapis.com/css2?family=Montserrat:wght@500;600;700&family=Roboto+Condensed:wght@400&family=Open+Sans:wght@400&display=swap">
<style>
:root{
  --navy:#0a3a73;
  --teal:#00706b;
  --black:#1a1a1a;
  --page:#ebebeb;
  --row-alt:#f0f0f0;
  --white:#ffffff;
  --grey-btn:#9b9b9b;
  --text:#111;
  --line:#e3e3e3;
  --blue:#3b6fb0;
  --olive:#b7b93a;
}
*{box-sizing:border-box;margin:0;padding:0}
html,body{width:1110px;height:1200px;overflow:hidden;background:var(--white)}
.stage{width:1300px;height:1405px;transform:scale(.853846);transform-origin:0 0;position:relative;font-family:"Montserrat",sans-serif}
.frame{position:absolute;left:15px;top:15px;width:1270px;height:1375px;background:linear-gradient(#e4e4e4,#f1f1f1 300px,#efefef)}
.nav{position:absolute;left:15px;top:15px;width:1270px;height:60px;background:var(--white);display:flex}
.brand{width:180px;display:flex;align-items:center;padding-left:58px;font-weight:700;font-size:17px;color:var(--black)}
.period{width:90px;display:flex;align-items:center;justify-content:center;font-weight:700;font-size:14px;border-right:1px solid var(--line)}
.period.active{background:var(--navy);color:var(--white)}
.nav-spacer{width:136px;border-right:1px solid var(--line)}
.nav-link{display:flex;align-items:center;justify-content:center;gap:8px;font-weight:700;font-size:13px;border-right:1px solid var(--line)}
.nav-link svg{width:24px;height:24px}
.pill{position:absolute;left:70px;height:40px;width:325px;border-radius:3px;color:var(--white);font-weight:600;font-size:16px;display:flex;align-items:center;justify-content:center}
.pill.selected{top:115px;background:var(--navy)}
.pill.unselected{top:500px;background:var(--grey-btn)}
.collapse{position:absolute;left:1199px;top:504px;width:32px;height:32px;border-radius:50%;border:2px solid #bbb;background:#2a2a2a;display:flex;align-items:center;justify-content:center}
table{border-collapse:collapse;font-family:"Roboto Condensed",sans-serif;font-size:17px;color:var(--text)}
.stats{position:absolute;left:70px;top:170px;width:1160px;box-shadow:0 2px 6px rgba(0,0,0,.08)}
.stats th{height:70px;color:var(--white);font-family:"Montserrat",sans-serif;font-weight:600;font-size:16px;background:var(--teal);width:180px;border-left:1px solid #0b5c58}
.stats th.id{background:var(--black);width:440px;border-left:none}
.stats td{height:69px;text-align:center;background:var(--white);border-left:1px solid #eee}
.stats tr:nth-child(even) td{background:var(--row-alt)}
.pool{position:absolute;left:70px;top:555px;width:1160px;box-shadow:0 2px 6px rgba(0,0,0,.08)}
.pool td{height:70px;width:232px;text-align:center;background:var(--white);border-left:1px solid #eee}
.pool tr:nth-child(odd) td{background:var(--row-alt)}
.chart-card{position:absolute;left:70px;top:885px;width:1160px;height:425px;background:var(--white);box-shadow:0 2px 8px rgba(0,0,0,.08)}
.chart-head{height:85px;background:var(--row-alt);position:relative}
.tab{position:absolute;height:35px;bottom:0;background:var(--white);font-size:13px;font-weight:600;display:flex;align-items:center;justify-content:center;color:#333}
.tab.chart{left:55px;width:155px;background:var(--navy);color:var(--white)}
.tab.active{background:var(--black);color:var(--white);height:45px}
.plot{position:absolute;left:0;top:0}
</style>
</head>
<body>
<div class="stage">
  <div class="frame"></div>
  <nav class="nav">
    <div class="brand">PELLWORTH</div>
    <div class="period active">250D</div>
    <div class="period">83D</div>
    <div class="period">42D</div>
    <div class="nav-spacer"></div>
    <div class="nav-link" style="width:140px;border-left:1px solid var(--line)">
      <svg viewBox="0 0 24 24"><path d="M3 12 12 4l9 8M6 10v10h4v-6h4v6h4V10" fill="none" stroke="#111" stroke-width="2.4"/></svg>MODELS</div>
    <div class="nav-link" style="width:177px">
      <svg viewBox="0 0 24 24" fill="#111"><circle cx="12" cy="12" r="3"/><circle cx="12" cy="3" r="1.6"/><circle cx="12" cy="21" r="1.6"/><circle cx="3" cy="12" r="1.6"/><circle cx="21" cy="12" r="1.6"/><circle cx="5.6" cy="5.6" r="1.6"/><circle cx="18.4" cy="18.4" r="1.6"/><circle cx="5.6" cy="18.4" r="1.6"/><circle cx="18.4" cy="5.6" r="1.6"/><circle cx="12" cy="7.5" r="1.2"/><circle cx="12" cy="16.5" r="1.2"/><circle cx="7.5" cy="12" r="1.2"/><circle cx="16.5" cy="12" r="1.2"/></svg>SENSITIVITIES</div>
    <div class="nav-link" style="width:160px">
      <svg viewBox="0 0 24 24" fill="none" stroke="#111" stroke-width="2"><circle cx="6.5" cy="6.5" r="4"/><circle cx="17.5" cy="6.5" r="4"/><circle cx="6.5" cy="17.5" r="4"/><circle cx="17.5" cy="17.5" r="4"/></svg>PORTFOLIO</div>
    <div class="nav-link" style="width:152px">
      <svg viewBox="0 0 24 24" fill="none" stroke="#111" stroke-width="2"><rect x="2" y="4" width="20" height="16"/><path d="M5 16l4-5 3 3 4-6 3 4"/></svg>BACKTEST</div>
  </nav>

  <div class="pill selected">Number of Selected Factors : 3</div>
  <table class="stats">
    <tr><th class="id">ID &#8964;</th><th>Stat 1</th><th>Stat 2</th><th>Stat 3</th><th>Stat 4</th></tr>
    <tr><td>Factor 1</td><td>-1.4</td><td>0.094</td><td>6.1</td><td>100</td></tr>
    <tr><td>Factor 2</td><td>2.8</td><td>0.085</td><td>3.1</td><td>0.7</td></tr>
    <tr><td>Factor 3</td><td>-3.7</td><td>2.7</td><td>-7.2</td><td>100</td></tr>
  </table>

  <div class="pill unselected">Unselected Factors</div>
  <div class="collapse"><svg width="16" height="16" viewBox="0 0 16 16"><path d="M3 11l5-5 5 5" fill="none" stroke="#fff" stroke-width="2.4"/></svg></div>
  <table class="pool">
    <tr><td>Factor</td><td>Factor</td><td>Factor</td><td>Factor</td><td>Factor</td></tr>
    <tr><td>Factor</td><td>Factor</td><td>Factor</td><td>Factor</td><td>Factor</td></tr>
    <tr><td>Factor</td><td>Factor</td><td>Factor</td><td>Factor</td><td>Factor</td></tr>
    <tr><td>Factor</td><td>Factor</td><td>Factor</td><td>Factor</td><td>Factor</td></tr>
  </table>

  <section class="chart-card">
    <div class="chart-head">
      <div class="tab chart">CHART</div>
      <div class="tab" style="left:215px;width:90px">#1</div>
      <div class="tab" style="left:310px;width:90px">#2</div>
      <div class="tab" style="left:405px;width:90px;height:40px">#3</div>
      <div class="tab active" style="left:500px;width:90px">#4</div>
    </div>
  </section>

  <svg class="plot" width="1300" height="1405" font-family="Open Sans, sans-serif" font-size="11" fill="#555">
    <g stroke="#eee">
      <line x1="155" y1="1033" x2="1075" y2="1033"/><line x1="155" y1="1070" x2="1075" y2="1070"/><line x1="155" y1="1108" x2="1075" y2="1108"/><line x1="155" y1="1145" x2="1075" y2="1145"/><line x1="155" y1="1183" x2="1075" y2="1183"/>
      <line x1="182" y1="1020" x2="182" y2="1220"/><line x1="325" y1="1020" x2="325" y2="1220"/><line x1="466" y1="1020" x2="466" y2="1220"/><line x1="606" y1="1020" x2="606" y2="1220"/><line x1="742" y1="1020" x2="742" y2="1220"/><line x1="883" y1="1020" x2="883" y2="1220"/><line x1="1023" y1="1020" x2="1023" y2="1220"/>
    </g>
    <line x1="155" y1="1220" x2="1075" y2="1220" stroke="#999"/>
    <g text-anchor="end"><text x="151" y="1037">100</text><text x="151" y="1074">80</text><text x="151" y="1112">60</text><text x="151" y="1149">40</text><text x="151" y="1187">20</text><text x="151" y="1224">0</text></g>
    <g text-anchor="middle"><text x="182" y="1245">Jul 2018</text><text x="325" y="1245">Sep 2018</text><text x="466" y="1245">Nov 2018</text><text x="606" y="1245">Jan 2019</text><text x="742" y="1245">Mar 2019</text><text x="883" y="1245">May 2019</text><text x="1023" y="1245">Jul 2019</text></g>

    <g stroke-linecap="round" stroke-width="8" fill="none">
      <line x1="202" y1="1034" x2="288" y2="1034" stroke="var(--olive)" stroke-dasharray="0 6"/>
      <line x1="750" y1="1036" x2="1000" y2="1036" stroke="var(--olive)" stroke-dasharray="0 7"/>
      <line x1="590" y1="1033" x2="1026" y2="1033" stroke="var(--blue)" stroke-dasharray="0 7"/>
      <line x1="999" y1="1216" x2="1010" y2="1216" stroke="#3c9a3c" stroke-dasharray="0 5"/>
    </g>
    <g fill="var(--olive)">
      <circle cx="290" cy="1045" r="4"/><circle cx="297" cy="1049" r="4"/><circle cx="302" cy="1036" r="4"/><circle cx="310" cy="1040" r="4"/><circle cx="316" cy="1036" r="4"/><circle cx="322" cy="1042" r="4"/><circle cx="333" cy="1044" r="4"/>
      <circle cx="336" cy="1099" r="4"/><circle cx="339" cy="1131" r="4"/><circle cx="344" cy="1140" r="4"/><circle cx="350" cy="1110" r="4"/><circle cx="354" cy="1132" r="4"/><circle cx="360" cy="1146" r="4"/><circle cx="366" cy="1135" r="4"/><circle cx="371" cy="1126" r="4"/><circle cx="376" cy="1138" r="4"/><circle cx="380" cy="1092" r="4"/><circle cx="385" cy="1098" r="4"/><circle cx="388" cy="1075" r="4"/><circle cx="393" cy="1063" r="4"/><circle cx="398" cy="1060" r="4"/><circle cx="401" cy="1034" r="4"/><circle cx="408" cy="1040" r="4"/><circle cx="413" cy="1107" r="4"/><circle cx="417" cy="1094" r="4"/><circle cx="421" cy="1118" r="4"/><circle cx="426" cy="1126" r="4"/><circle cx="430" cy="1114" r="4"/>
      <circle cx="434" cy="1196" r="4"/><circle cx="440" cy="1189" r="4"/><circle cx="446" cy="1183" r="4"/><circle cx="452" cy="1196" r="4"/><circle cx="458" cy="1178" r="4"/><circle cx="464" cy="1205" r="4"/><circle cx="469" cy="1215" r="4"/><circle cx="475" cy="1210" r="4"/><circle cx="481" cy="1212" r="4"/><circle cx="486" cy="1200" r="4"/><circle cx="491" cy="1206" r="4"/><circle cx="496" cy="1167" r="4"/><circle cx="501" cy="1188" r="4"/><circle cx="507" cy="1178" r="4"/><circle cx="513" cy="1165" r="4"/><circle cx="519" cy="1148" r="4"/><circle cx="524" cy="1158" r="4"/><circle cx="528" cy="1116" r="4"/><circle cx="533" cy="1106" r="4"/><circle cx="539" cy="1110" r="4"/><circle cx="542" cy="1035" r="4"/><circle cx="548" cy="1038" r="4"/><circle cx="554" cy="1034" r="4"/>
      <circle cx="575" cy="1207" r="4"/><circle cx="580" cy="1212" r="4"/><circle cx="592" cy="1204" r="4"/><circle cx="598" cy="1210" r="4"/><circle cx="604" cy="1198" r="4"/><circle cx="610" cy="1192" r="4"/><circle cx="616" cy="1202" r="4"/><circle cx="622" cy="1194" r="4"/><circle cx="628" cy="1200" r="4"/><circle cx="634" cy="1207" r="4"/><circle cx="639" cy="1196" r="4"/><circle cx="645" cy="1182" r="4"/><circle cx="651" cy="1168" r="4"/><circle cx="656" cy="1168" r="4"/><circle cx="659" cy="1134" r="4"/><circle cx="661" cy="1147" r="4"/><circle cx="654" cy="1097" r="4"/><circle cx="667" cy="1097" r="4"/><circle cx="670" cy="1060" r="4"/><circle cx="673" cy="1053" r="4"/><circle cx="688" cy="1055" r="4"/><circle cx="691" cy="1108" r="4"/><circle cx="694" cy="1176" r="4"/><circle cx="700" cy="1180" r="4"/><circle cx="703" cy="1190" r="4"/><circle cx="705" cy="1054" r="4"/><circle cx="708" cy="1090" r="4"/><circle cx="712" cy="1066" r="4"/><circle cx="716" cy="1088" r="4"/><circle cx="720" cy="1133" r="4"/><circle cx="722" cy="1040" r="4"/><circle cx="728" cy="1058" r="4"/><circle cx="733" cy="1050" r="4"/><circle cx="738" cy="1046" r="4"/><circle cx="744" cy="1040" r="4"/><circle cx="750" cy="1048" r="4"/>
    </g>
    <g fill="var(--blue)">
      <circle cx="203" cy="1098" r="4"/><circle cx="206" cy="1045" r="4"/><circle cx="210" cy="1038" r="4"/><circle cx="216" cy="1044" r="4"/><circle cx="221" cy="1044" r="4"/><circle cx="224" cy="1113" r="4"/><circle cx="227" cy="1146" r="4"/><circle cx="233" cy="1142" r="4"/><circle cx="236" cy="1160" r="4"/><circle cx="239" cy="1176" r="4"/><circle cx="242" cy="1162" r="4"/><circle cx="247" cy="1150" r="4"/><circle cx="251" cy="1168" r="4"/><circle cx="255" cy="1110" r="4"/><circle cx="259" cy="1135" r="4"/><circle cx="264" cy="1135" r="4"/><circle cx="268" cy="1112" r="4"/><circle cx="272" cy="1135" r="4"/><circle cx="275" cy="1174" r="4"/><circle cx="281" cy="1174" r="4"/><circle cx="285" cy="1167" r="4"/><circle cx="288" cy="1150" r="4"/><circle cx="292" cy="1140" r="4"/><circle cx="297" cy="1146" r="4"/><circle cx="300" cy="1175" r="4"/><circle cx="304" cy="1163" r="4"/><circle cx="309" cy="1170" r="4"/><circle cx="314" cy="1165" r="4"/><circle cx="318" cy="1172" r="4"/><circle cx="323" cy="1175" r="4"/><circle cx="333" cy="1180" r="4"/><circle cx="337" cy="1198" r="4"/><circle cx="343" cy="1200" r="4"/><circle cx="348" cy="1196" r="4"/><circle cx="352" cy="1190" r="4"/><circle cx="357" cy="1196" r="4"/><circle cx="362" cy="1200" r="4"/><circle cx="367" cy="1195" r="4"/><circle cx="372" cy="1190" r="4"/><circle cx="378" cy="1177" r="4"/><circle cx="383" cy="1170" r="4"/><circle cx="388" cy="1168" r="4"/><circle cx="393" cy="1162" r="4"/><circle cx="398" cy="1166" r="4"/><circle cx="402" cy="1183" r="4"/><circle cx="407" cy="1172" r="4"/><circle cx="411" cy="1186" r="4"/><circle cx="416" cy="1170" r="4"/><circle cx="421" cy="1182" r="4"/><circle cx="426" cy="1190" r="4"/><circle cx="431" cy="1168" r="4"/><circle cx="434" cy="1217" r="4"/><circle cx="441" cy="1170" r="4"/><circle cx="446" cy="1210" r="4"/><circle cx="450" cy="1186" r="4"/><circle cx="456" cy="1192" r="4"/><circle cx="460" cy="1162" r="4"/><circle cx="463" cy="1090" r="4"/><circle cx="466" cy="1063" r="4"/><circle cx="470" cy="1058" r="4"/><circle cx="474" cy="1067" r="4"/><circle cx="478" cy="1072" r="4"/><circle cx="480" cy="1046" r="4"/><circle cx="483" cy="1054" r="4"/><circle cx="488" cy="1070" r="4"/><circle cx="493" cy="1198" r="4"/><circle cx="497" cy="1193" r="4"/><circle cx="500" cy="1185" r="4"/><circle cx="506" cy="1177" r="4"/><circle cx="510" cy="1172" r="4"/><circle cx="514" cy="1172" r="4"/><circle cx="519" cy="1173" r="4"/><circle cx="525" cy="1186" r="4"/><circle cx="529" cy="1150" r="4"/><circle cx="533" cy="1138" r="4"/><circle cx="539" cy="1140" r="4"/><circle cx="542" cy="1054" r="4"/><circle cx="546" cy="1049" r="4"/><circle cx="551" cy="1040" r="4"/><circle cx="557" cy="1042" r="4"/><circle cx="562" cy="1044" r="4"/><circle cx="567" cy="1046" r="4"/><circle cx="572" cy="1048" r="4"/><circle cx="577" cy="1035" r="4"/>
    </g>

    <g>
      <text x="1132" y="1035" font-family="Times New Roman, serif" fill="#444">Names</text>
      <circle cx="1114" cy="1031" r="3.5" fill="#8ab0dc"/><circle cx="1114" cy="1050" r="3.5" fill="#f3b27a"/><circle cx="1114" cy="1069" r="3.5" fill="#3c9a3c"/><circle cx="1114" cy="1087" r="3.5" fill="#e07070"/><circle cx="1114" cy="1106" r="3.5" fill="#c4a6dc"/><circle cx="1114" cy="1125" r="3.5" fill="#b79a90"/><circle cx="1114" cy="1143" r="3.5" fill="#eaa6d4"/><circle cx="1114" cy="1162" r="3.5" fill="#bcbcbc"/><circle cx="1114" cy="1181" r="3.5" fill="var(--olive)"/><circle cx="1114" cy="1199" r="3.5" fill="#8ad8e4"/><circle cx="1114" cy="1218" r="3.5" fill="var(--blue)"/>
    </g>
  </svg>
</div>
</body>
</html>
```